Mexican Restaurant needs a new Menu Design

Mexican restaurant LA MARIPOSA AZUL is renewing its menu, so we need something new.
Since our inception we have given the task of rescuing ingredients, recipes, and traditional and representatives dishes of the culinary techniques of yesteryear.
We are the only restaurant in Guadalajara that manufactures its own dairy natural as fresh cheese, the cream and our already well-known and traditional jocoqui. In addition, we produce organic ranch egg and are currently in the development of organic vegetables cultivated on the slopes of the old Hill which gives our plants benefit from an exceptional microclimate.
Find more information about the restaurant in www.lamariposaazul.com.
The menu needs to have the full list of products with the prices, some phrases that speak of the philosophy of the ranch-style-living, photos.
We need the cover, back cover and interiors.
Updates
Thank you so much for the proposals you have submitted for the menu design. We are looking them carefully.
Thank you very much for taking your time to design a proposal for our menu!!!
Target Market(s)
The target is very wide (28-40 yrs.): Young executives, Young families, Housewives.
Industry/Entity Type
Restaurant
Look and feel
Each slider illustrates characteristics of the customer's brand and the style your logo design should communicate.

```html
<!DOCTYPE html>
<html lang="es">
<head>
<meta charset="utf-8">
<title>La Mariposa Azul — Menu Cover</title>
<link rel="stylesheet" href="https://fonts.googleapis.com/css2?family=Arimo&family=Cormorant+Garamond:ital,wght@0,500;1,600&family=Cormorant+SC:wght@500&display=swap">
<style>
  :root {
    --canvas: #efefef;
    --label: #333333;
    --red: #e2070a;
    --red-deep: #9c0003;
    --red-shadow: #3a0000;
    --badge: #e8220f;
    --white: #ffffff;
    --ink: #111111;
  }
  * { margin: 0; padding: 0; box-sizing: border-box; }
  html, body { width: 1200px; height: 901px; overflow: hidden; background: var(--canvas); }
  .canvas { position: relative; width: 1200px; height: 901px; }

  .panel {
    position: absolute; top: 31px; width: 569px; height: 826px; overflow: hidden;
    background:
      radial-gradient(ellipse 75% 70% at 50% 50%, var(--red) 45%, rgba(226,7,10,0) 100%),
      radial-gradient(ellipse 120% 110% at 50% 50%, var(--red) 30%, var(--red-deep) 80%, var(--red-shadow) 100%);
  }
  .panel--back { left: 22px; }
  .panel--front { left: 612px; }

  .panel-label {
    position: absolute; top: 858px; font: 36px "Arimo", Arial, sans-serif; color: var(--label);
  }
  .panel-label--back { left: 35px; }
  .panel-label--front { left: 627px; }

  .name-badge {
    position: absolute; background: var(--badge); color: var(--white); text-align: right;
  }
  .name-badge::before {
    content: ""; position: absolute; inset: 9px; border: 2px solid var(--white);
  }
  .name-badge__name {
    display: block; font-family: "Cormorant SC", "Cormorant Garamond", serif; font-weight: 500;
    white-space: nowrap; text-align: center;
  }
  .name-badge__tag {
    display: block; font-family: "Cormorant Garamond", serif; font-weight: 500;
  }
  .panel--back .name-badge { left: 91px; top: 177px; width: 357px; height: 158px; padding: 41px 33px 0 20px; }
  .panel--back .name-badge__name { font-size: 36px; line-height: 46px; margin-left: 10px; }
  .panel--back .name-badge__tag { font-size: 20px; line-height: 22px; }
  .panel--front .name-badge { left: 31px; top: 51px; width: 507px; height: 216px; padding: 54px 47px 0 30px; }
  .panel--front .name-badge__name { font-size: 51px; line-height: 64px; margin-left: 17px; }
  .panel--front .name-badge__tag { font-size: 28px; line-height: 30px; }

  .contact {
    position: absolute; left: 36px; top: 455px; font: 21px/29px "Arimo", Arial, sans-serif;
    color: var(--white); font-style: normal;
  }
  .contact__address { margin-bottom: 12px; }
  .contact__label { color: var(--ink); }
  .contact__phones { display: flex; gap: 8px; margin-bottom: 11px; }
  .contact__phones .contact__label { line-height: 24px; }
  .contact__email { margin-top: 6px; }

  .mascot-art {
    position: absolute; left: 116px; top: 274px; width: 384px; height: 376px;
    border-radius: 45% 45% 35% 35%;
    background: radial-gradient(ellipse at 50% 45%, #c89050 0%, #9b1b3a 55%, rgba(226,7,10,0) 75%);
  }
  .tagline {
    position: absolute; left: 0; right: 0; top: 638px; text-align: center;
    font-family: "Cormorant Garamond", serif; font-style: italic; font-weight: 600;
    font-size: 60px; color: var(--white); white-space: nowrap;
  }
  .flourish {
    position: absolute; left: 160px; top: 722px; width: 250px; height: 50px;
    background: radial-gradient(ellipse at 50% 50%, rgba(255,255,255,0.55) 0%, rgba(255,255,255,0) 70%);
  }
</style>
</head>
<body>
<main class="canvas">
  <section class="panel panel--back">
    <div class="name-badge">
      <span class="name-badge__name">La Mariposa Azul</span>
      <span class="name-badge__tag">Restaurante</span>
    </div>
    <address class="contact">
      <div class="contact__address">
        Av. Las Palmas #1840<br>
        Col. Arboledas del Sur<br>
        Zapopan, Jalisco<br>
        44190
      </div>
      <div class="contact__phones">
        <span class="contact__label">Teléfonos:</span>
        <span>01(33)35 12 40 61<br>01(33)35 12 40 62</span>
      </div>
      <div class="contact__label">Correo Electrónico:</div>
      <div class="contact__email">reservaciones@lamariposaazul.com</div>
    </address>
  </section>

  <section class="panel panel--front">
    <div class="name-badge">
      <span class="name-badge__name">La Mariposa Azul</span>
      <span class="name-badge__tag">Restaurante</span>
    </div>
    <div class="mascot-art" role="img" aria-label="Illustrated cartoon mascot in a charro outfit and sombrero twirling a lasso"></div>
    <p class="tagline">Open 7 Days a week</p>
    <div class="flourish" role="img" aria-label="White decorative flourish ornament"></div>
  </section>

  <span class="panel-label panel-label--back">Back</span>
  <span class="panel-label panel-label--front">Front</span>
</main>
</body>
</html>
```